Webdesign für Installation, Wartung und Modernisierung von Heizungsanlagen, Lüftungsanlagen und Sanitäranlagen
Zielgruppe
Installation, Wartung und Modernisierung von Heizungsanlagen, Lüftungsanlagen und Sanitäranlagen
Zielgruppe: Firmen und Unternehmen aus der Immobilienwirtschaft, der Industrie sowie Privathaushalte
Aufgabenstellung
- in Adobe Photoshop
- nur die Startseite layouten
- Farben an das Logo angelehnt
- es soll einen blauen Streifen im Projekt geben. siehe pdf Logo

```html
<!DOCTYPE html>
<html lang="de">
<head>
<meta charset="utf-8">
<title>Haustechnik Kranzbach GmbH – Startseite</title>
<link href="https://fonts.googleapis.com/css2?family=Arimo:wght@400;700&display=swap" rel="stylesheet">
<style>
:root{
  --blue:#3b5c95;
  --blue-dark:#2f4d82;
  --blue-light:#6d88b8;
  --red:#c43a35;
  --text:#2b2b2b;
  --muted:#555;
  --grey-bg:#f1f1f1;
  --white:#fff;
}
*{box-sizing:border-box;margin:0;padding:0}
html,body{width:1200px;height:3999px;overflow:hidden}
body{position:relative;background:var(--white);font-family:"Arimo",Arial,sans-serif;color:var(--text)}
.abs{position:absolute}
.stripes{background:repeating-linear-gradient(180deg,var(--blue) 0 3px,var(--blue-light) 3px 4px)}

/* header */
.brand{left:175px;top:34px;display:flex;align-items:center;gap:10px}
.brand-mark{width:14px;height:14px;background:var(--blue)}
.brand-name{font-size:19px;font-weight:400;color:var(--blue)}
.contact-top{right:175px;top:26px;text-align:right;font-size:11px;line-height:14px;color:var(--text)}
.contact-top .phone{font-size:17px;color:var(--blue);line-height:22px;display:flex;align-items:center;justify-content:flex-end;gap:6px}
.nav{left:0;top:110px;width:1200px;height:27px}
.nav ul{list-style:none;display:flex;gap:37px;padding-left:175px;height:100%;align-items:center}
.nav li{color:var(--white);font-size:13px;letter-spacing:.2px}

/* hero */
.hero{left:0;top:137px;width:1200px;height:579px;background:linear-gradient(135deg,#c9c6bf 0%,#9aa0a6 40%,#5a5f66 60%,#d8d4cc 100%)}
.hero-band{left:0;top:337px;width:1200px;height:129px;background:rgba(59,92,149,.72);display:flex;align-items:center;justify-content:center}
.hero-band h1{color:var(--white);font-size:50px;line-height:60px;text-align:center;font-weight:700}

/* headings */
.sec-title{left:0;width:1200px;text-align:center;font-size:22px;font-weight:400;color:var(--text);letter-spacing:.3px}
.sec-title::after{content:"";display:block;width:160px;height:2px;background:var(--red);margin:10px auto 0}

/* cards */
.card{background:var(--white);box-shadow:0 2px 6px rgba(0,0,0,.15)}
.card .ph{position:absolute;left:0;top:0;width:100%}
.card .cap{position:absolute;left:0;bottom:0;width:100%;text-align:center;font-size:14px;letter-spacing:.3px}
.card .cap span{border-bottom:2px solid var(--red);padding-bottom:1px}
.card.active{background:var(--blue)}
.card.active .cap{color:var(--white)}

.panel{background:var(--blue);color:var(--white);text-align:center}
.panel h2{font-size:21px;font-weight:400;line-height:25px}
.panel p{font-size:14.5px;line-height:25px}
.btn{position:absolute;border-radius:20px;font-size:14px;display:flex;align-items:center;justify-content:center;letter-spacing:.2px}
.btn-outline{border:3px solid var(--blue);color:var(--text);background:var(--white)}
.btn-solid{background:var(--blue);color:var(--white)}

.about{left:175px;top:2465px;width:850px;text-align:center;font-size:14.5px;line-height:25px;color:var(--text)}
.member{width:160px;text-align:center;font-size:12px}
.member .avatar{width:152px;height:152px;border-radius:50%;margin:0 auto 22px;background:radial-gradient(circle at 50% 40%,#b9a99a,#6b6560)}

.jobs-bg{left:0;top:2983px;width:1200px;height:490px;background:var(--grey-bg)}
.dot{width:12px;height:12px;border-radius:50%;border:2px solid var(--blue)}

.contact-panel{left:599px;top:3562px;width:601px;height:248px;background:var(--blue)}
.contact-panel h2{position:absolute;left:39px;top:26px;color:var(--white);font-size:21px;font-weight:400}
.field{position:absolute;background:var(--white);border-radius:3px;font-size:11px;color:#aaa;font-style:italic;padding:8px 7px}
.send{position:absolute;left:287px;top:197px;width:148px;height:30px;border:2px solid var(--white);border-radius:16px;color:var(--white);font-size:14px;display:flex;align-items:center;justify-content:center}

.footer{left:0;top:3876px;width:1200px;height:123px;background:var(--blue);color:var(--white);font-size:11px;text-align:center}
.footer .bottom{position:absolute;left:0;bottom:0;width:100%;height:20px;line-height:20px}
</style>
</head>
<body>

<header>
  <div class="abs brand"><span class="brand-mark"></span><span class="brand-name">Haustechnik Kranzbach GmbH</span></div>
  <div class="abs contact-top">
    <div class="phone"><svg width="16" height="16" viewBox="0 0 24 24"><path fill="#3b5c95" d="M6.6 10.8a15 15 0 006.6 6.6l2.2-2.2c.3-.3.7-.4 1-.2 1.1.4 2.3.6 3.6.6.6 0 1 .4 1 1V20c0 .6-.4 1-1 1A17 17 0 013 4c0-.6.4-1 1-1h3.5c.6 0 1 .4 1 1 0 1.3.2 2.5.6 3.6.1.3 0 .7-.2 1z"/></svg>(03771) 482915</div>
    <div>info@haustechnik-kranzbach.de</div>
    <div>Montag-Freitag: 09:00 - 12:00</div>
    <div>14:00 - 17:00</div>
  </div>
  <nav class="abs nav stripes">
    <ul><li>UNTERNEHMEN</li><li>HEIZUNG</li><li>LÜFTUNG</li><li>SANITÄR</li><li>DACHKLEMPNEREI</li><li>ROHRLEITUNGSBAU</li><li>KONTAKT</li></ul>
  </nav>
</header>

<section>
  <div class="abs hero" role="img" aria-label="Foto: Fachleute mit Helm und Tablet über Bauplänen"></div>
  <div class="abs hero-band"><h1>Wir bieten Lösungen für Ihre<br>Gebäudetechnik</h1></div>
</section>

<section>
  <h2 class="abs sec-title" style="top:748px">UNSERE LEISTUNGEN</h2>
  <div class="abs card" style="left:175px;top:818px;width:418px;height:330px">
    <div class="ph" style="height:273px;background:linear-gradient(135deg,#e9e7e4,#9aa4b0)" role="img" aria-label="Foto: Handwerker montiert einen Heizkörper"></div>
    <div class="cap" style="height:57px;line-height:57px"><span>HEIZUNG</span></div>
  </div>
  <div class="abs card" style="left:607px;top:818px;width:421px;height:330px">
    <div class="ph" style="height:273px;background:radial-gradient(circle at 65% 55%,#e8eaee,#7e8fa8 60%,#4a5c78)" role="img" aria-label="Foto: Lüftungsventilator mit Schutzgitter"></div>
    <div class="cap" style="height:57px;line-height:57px"><span>LÜFTUNG</span></div>
  </div>
  <div class="abs card" style="left:172px;top:1173px;width:277px;height:329px">
    <div class="ph" style="height:275px;background:linear-gradient(135deg,#d8d2c8,#eeece8)" role="img" aria-label="Foto: helles Badezimmer mit Dusche"></div>
    <div class="cap" style="height:54px;line-height:54px"><span>SANITÄR</span></div>
  </div>
  <div class="abs card active" style="left:462px;top:1173px;width:275px;height:329px">
    <div class="ph" style="height:275px;background:linear-gradient(160deg,#b6c2d2,#6c7683)" role="img" aria-label="Foto: Metalldach eines Wohnhauses"></div>
    <div class="cap" style="height:54px;line-height:54px"><span>DACHKLEMPNEREI</span></div>
  </div>
  <div class="abs card" style="left:751px;top:1173px;width:275px;height:329px">
    <div class="ph" style="height:275px;background:linear-gradient(180deg,#d7d9dc,#bfc3c7)" role="img" aria-label="Foto: Wasserrohre mit Absperrventil"></div>
    <div class="cap" style="height:54px;line-height:54px"><span>ROHRLEITUNGSBAU</span></div>
  </div>
</section>

<section>
  <h2 class="abs sec-title" style="top:1577px">FÜR UNSERE KUNDEN</h2>
  <div class="abs panel" style="left:591px;top:1685px;width:609px;height:250px;padding:24px 0 0 30px">
    <h2>ZUM KOSTENLOSEN<br>HEIZUNGSANGEBOT</h2>
    <p style="margin-top:6px">Lorem ipsum dolor sit amet, consetetur sadipscing<br>elitr, sed diam nonumy eirmod tempor invidunt ut<br>labore et dolore magna aliquyam erat, sed diam<br>voluptua. At vero eos et accusam et justo duo dolores<br>et ea rebum. Stet clita kasd gubergren, no sea</p>
  </div>
  <div class="abs card" style="left:172px;top:1648px;width:419px;height:329px">
    <div class="ph" style="height:244px;background:linear-gradient(120deg,#7a5a4a,#e6e2dd 55%,#f4f2ef)" role="img" aria-label="Foto: Hand stellt Heizkörperthermostat ein"></div>
    <div class="btn btn-outline" style="left:92px;top:269px;width:245px;height:40px">HEIZUNGSKONFIGURATOR</div>
  </div>

  <div class="abs panel" style="left:0;top:2042px;width:610px;height:250px;padding:28px 0 0">
    <h2>LOREM IPSUM</h2>
    <p style="margin-top:18px">Lorem ipsum dolor sit amet, consetetur sadipscing<br>elitr, sed diam nonumy eirmod tempor invidunt ut<br>labore et dolore magna aliquyam erat, sed diam<br>voluptua. At vero eos et accusam et justo duo dolores<br>et ea rebum. Stet clita kasd gubergren, no sea</p>
  </div>
  <div class="abs card" style="left:608px;top:2002px;width:420px;height:331px">
    <div class="abs" style="left:28px;top:22px;width:359px;height:157px;background:linear-gradient(90deg,#cfd6d4,#5f7b78 50%,#2f8f8a)" role="img" aria-label="Titelseiten des Norvello-Gesamtkatalogs"></div>
    <p class="abs" style="left:0;top:188px;width:420px;text-align:center;font-size:14.5px;line-height:25px">Lorem ipsum dolor sit amet, consetetur sadipscing<br>elitr, sed diam nonumy eirmod tempor invidunt ut</p>
    <div class="btn btn-solid" style="left:90px;top:267px;width:247px;height:43px">NORVELLO GESAMTKATALOG</div>
  </div>
</section>

<section>
  <h2 class="abs sec-title" style="top:2392px">UNTERNEHMEN</h2>
  <p class="abs about">Lorem ipsum dolor sit amet, consetetur sadipscing elitr, sed diam nonumy eirmod tempor invidunt ut labore et dolore magna aliquyam erat, sed diam voluptua. At vero eos et accusam et justo duo dolores et ea rebum. Stet clita kasd gubergren, no sea takimata sanctus est Lorem ipsum dolor sit amet. Lorem ipsum dolor sit amet, consetetur sadipscing elitr, sed diam nonumy eirmod tempor invidunt ut labore et dolore magna aliquyam erat, sed diam voluptua. At vero eos et accusam et justo duo dolores et ea rebum. Stet clita kasd gubergren, no sea takimata sanctus est Lorem ipsum dolor sit amet.<br>Lorem ipsum dolor sit amet, consetetur sadipscing elitr, sed diam nonumy eirmod tempor invidunt ut labore et dolore magna aliquyam erat, sed diam voluptua. At vero eos et accusam et justo duo dolores et ea rebum. Stet clita kasd gubergren, no sea takimata sanctus est Lorem ipsum dolor sit amet. Lorem ipsum dolor sit amet, consetetur sadipscing</p>
  <svg class="abs" style="left:172px;top:2800px" width="18" height="24" viewBox="0 0 18 24"><path d="M13 3L5 12l8 9" fill="none" stroke="#3b5c95" stroke-width="3"/></svg>
  <svg class="abs" style="left:990px;top:2800px" width="18" height="24" viewBox="0 0 18 24"><path d="M5 3l8 9-8 9" fill="none" stroke="#3b5c95" stroke-width="3"/></svg>
  <div class="abs member" style="left:223px;top:2735px"><div class="avatar" role="img" aria-label="Porträtfoto Mitarbeiter"></div>Max Mustermann</div>
  <div class="abs member" style="left:420px;top:2735px"><div class="avatar" role="img" aria-label="Porträtfoto Mitarbeiter"></div>Max Mustermann</div>
  <div class="abs member" style="left:618px;top:2735px"><div class="avatar" role="img" aria-label="Porträtfoto Mitarbeiter"></div>Max Mustermann</div>
  <div class="abs member" style="left:812px;top:2735px"><div class="avatar" role="img" aria-label="Porträtfoto Mitarbeiter"></div>Max Mustermann</div>
</section>

<section>
  <div class="abs jobs-bg"></div>
  <h2 class="abs sec-title" style="top:3001px">FREIE STELLEN</h2>
  <div class="abs card" style="left:172px;top:3075px;width:277px;height:330px">
    <div class="ph" style="height:274px;background:linear-gradient(135deg,#8d9bb3,#3f5f9c 55%,#cfd3da)" role="img" aria-label="Foto: zwei Monteure mit Helm lesen einen Plan"></div>
    <div class="cap" style="height:56px;line-height:56px"><span>LOREM IPSUM</span></div>
  </div>
  <div class="abs card" style="left:462px;top:3075px;width:275px;height:330px">
    <div class="ph" style="height:274px;background:linear-gradient(135deg,#d6cdb8,#7a8088 55%,#cfcac2)" role="img" aria-label="Foto: Tablet mit Gebäudemodell über Bauplänen"></div>
    <div class="cap" style="height:56px;line-height:56px"><span>LOREM IPSUM</span></div>
  </div>
  <div class="abs card" style="left:750px;top:3075px;width:275px;height:330px">
    <div class="ph" style="height:274px;background:linear-gradient(135deg,#e9e7e4,#9aa4b0)" role="img" aria-label="Foto: Handwerker montiert einen Heizkörper"></div>
    <div class="cap" style="height:56px;line-height:56px"><span>LOREM IPSUM</span></div>
  </div>
  <div class="abs dot" style="left:574px;top:3446px;background:var(--blue)"></div>
  <div class="abs dot" style="left:593px;top:3446px"></div>
  <div class="abs dot" style="left:612px;top:3446px"></div>
</section>

<section>
  <div class="abs" style="left:175px;top:3520px;width:424px;height:334px;background:linear-gradient(135deg,#e8eaed,#dfe6dc 50%,#e4e8ee)" role="img" aria-label="Stadtplan mit Firmenstandort"></div>
  <div class="abs contact-panel">
    <h2>KONTAKTIEREN SIE UNS!</h2>
    <div class="field" style="left:39px;top:60px;width:186px;height:30px">Nachname</div>
    <div class="field" style="left:39px;top:104px;width:186px;height:30px">Vorname</div>
    <div class="field" style="left:39px;top:147px;width:186px;height:30px">Email</div>
    <div class="field" style="left:245px;top:60px;width:204px;height:117px">Ihre Nachricht....</div>
    <div class="send">Weiter</div>
  </div>
</section>

<footer class="abs footer">
  <div style="position:absolute;top:18px;width:100%;font-weight:700">Haustechnik Kranzbach GmbH</div>
  <div style="position:absolute;top:44px;left:0;width:100%;display:flex;justify-content:center;gap:20px;line-height:14px;text-align:left">
    <div>Lindenstraße 14<br>08280 Talheim</div>
    <div>T: 03771 482915<br>F: 03771 482917</div>
  </div>
  <div style="position:absolute;top:82px;width:100%">E: info@haustechnik-kranzbach.de</div>
  <div class="bottom stripes">© Haustechnik Kranzbach GmbH 2022 | All rights reserved. | Impressum | Datenschutz</div>
</footer>

</body>
</html>
```